Business Cards for a law firm

Business cards for our law firm. Use our silhoette logo and OAK PARTNERS - check our website (www.oakpartners.example)

Contact Information for Business Card

our silhouette logo, OAK PARTNERS, 800-555-0147, Dorian Pemberton, dorian@oakpartners.example

Requirements
Must have
• our silhouette logo, OAK PARTNERS, 800-555-0147, Dorian Pemberton, dorian@oakpartners.example

```html
<!DOCTYPE html>
<html lang="en">
<head>
<meta charset="utf-8">
<title>Oak Partners — Business Cards</title>
<link rel="stylesheet" href="https://fonts.googleapis.com/css2?family=Archivo:wght@400;700&family=Cinzel:wght@700&display=swap">
<style>
  :root {
    --navy: #00139d;
    --green: #2ee87a;
    --white: #ffffff;
    --backdrop: #e4e4e4;
    --ink: #111111;
  }
  * { margin: 0; padding: 0; box-sizing: border-box; }
  html, body { width: 1200px; height: 1200px; overflow: hidden; }
  body { background: var(--backdrop); position: relative; font-family: "Archivo", Arial, sans-serif; }
  .card { position: absolute; left: 215px; width: 769px; height: 440px; background: var(--white); }
  .card--front { top: 141px; }
  .card--back { top: 619px; }
  .card svg { display: block; width: 100%; height: 100%; }
  .fill-navy { fill: var(--navy); }
  .fill-green { fill: var(--green); }
  .rule { fill: none; stroke: var(--navy); stroke-width: 3; }
  .icon { fill: none; stroke: var(--white); stroke-width: 3.5; stroke-linecap: round; stroke-linejoin: round; }
  .icon-solid { fill: var(--white); }
  .name { font-family: "Archivo", Arial, sans-serif; font-weight: 700; font-size: 62px; }
  .name__first { fill: var(--navy); }
  .name__last { fill: var(--green); }
  .contact { font-family: "Archivo", Arial, sans-serif; font-weight: 400; font-size: 26px; fill: var(--ink); }
  .firm { font-family: "Cinzel", Georgia, serif; font-weight: 700; fill: var(--navy); }
</style>
</head>
<body>

<section class="card card--front" aria-label="Business card front">
  <svg viewBox="0 0 1239 708" xmlns="http://www.w3.org/2000/svg">
    <rect class="fill-green accent-bar" x="37" y="0" width="51" height="122"/>

    <polygon class="fill-navy" points="807,0 872,0 658,530 1095,708 936,708 579,563"/>
    <polygon class="fill-green" points="872,0 922,0 719,505 1219,708 1095,708 658,530"/>
    <polyline class="rule" points="952,0 754,489 1239,685"/>

    <text class="name" x="35" y="198"><tspan class="name__first">Dorian</tspan> <tspan class="name__last">Pemberton</tspan></text>

    <g class="contact-tags">
      <polygon class="fill-green" points="37,346 80,321 80,381 37,407"/>
      <polygon class="fill-green" points="37,418 80,393 80,453 37,479"/>
      <polygon class="fill-green" points="37,490 80,465 80,525 37,551"/>
      <polygon class="fill-green" points="37,562 80,537 80,598 37,623"/>

      <path class="icon" d="M48,356 q-2,8 6,16 q8,8 16,6 l0,-5 l-6,-3 l-3,3 q-6,-3 -8,-8 l3,-3 l-3,-6 z"/>
      <g class="icon"><rect x="44" y="427" width="29" height="20" rx="2"/><polyline points="44,429 58.5,440 73,429"/></g>
      <g class="icon" stroke-width="2.5"><circle cx="58.5" cy="508" r="14"/><ellipse cx="58.5" cy="508" rx="6" ry="14"/><line x1="44.5" y1="508" x2="72.5" y2="508"/><line x1="46.5" y1="501" x2="70.5" y2="501"/><line x1="46.5" y1="515" x2="70.5" y2="515"/></g>
      <path class="icon-solid" d="M58.5,565 a11,11 0 0 1 11,11 c0,8 -11,20 -11,20 c0,0 -11,-12 -11,-20 a11,11 0 0 1 11,-11 z M58.5,571 a5,5 0 1 0 0.01,0 z" fill-rule="evenodd"/>
    </g>

    <g class="contact">
      <text x="97" y="373">800-555-0147</text>
      <text x="97" y="443">dorian@oakpartners.example</text>
      <text x="97" y="515">www.oakpartners.example</text>
      <text x="97" y="587">Your Street,City,State,</text>
      <text x="97" y="621">Pin Code,Country</text>
    </g>

    <text class="firm firm--small" x="1037" y="362" font-size="26" text-anchor="middle">OAK PARTNERS</text>
  </svg>
</section>

<section class="card card--back" aria-label="Business card back">
  <svg viewBox="0 0 1239 708" xmlns="http://www.w3.org/2000/svg">
    <g class="chevron chevron--left">
      <polygon class="fill-navy" points="0,0 315,127 82,708 14,708 234,161 0,67"/>
      <polygon class="fill-green" points="0,67 234,161 14,708 0,708 0,608 171,187 0,118"/>
      <polyline class="rule" points="0,149 136,203 0,538"/>
    </g>
    <g class="chevron chevron--right">
      <polygon class="fill-navy" points="1239,0 924,127 1157,708 1225,708 1005,161 1239,67"/>
      <polygon class="fill-green" points="1239,67 1005,161 1225,708 1239,708 1239,608 1068,187 1239,118"/>
      <polyline class="rule" points="1239,149 1103,203 1239,538"/>
    </g>

    <rect class="fill-navy brand-mark" x="574" y="250" width="92" height="92"/>
    <text class="firm firm--large" x="619.5" y="493" font-size="76" text-anchor="middle">OAK PARTNERS</text>
  </svg>
</section>

</body>
</html>
```